real esate business card with company logo and name

we need a business card design for a real esate company

The company name is Walsh & Brand Pty Ltd, and we have our logo designed and will upload. We want classic or moden feel. Black or white background. looks more textured. Should include folowinginformations
Owen Walsh and Lucy Brand
Sales Agents & Onsite Manager
p: 07 5948 2063
F: 07 5948 2174
M:0431 857 219
3/42 Marlow Crescent, FERNLEA QLD 4213

We want this business card looks professonal. Thank you in advance.

Industry/Entity Type

Real Estate Agent

Contact Information for Business Card

Owen Walsh and Lucy Brand
Onsite Manager & Sales Agents
p: 07 5948 2063
M:0431 857 219

Font styles to use
Serif

Colors
000000
fbfbfb
333333
959595

Requirements
Must have
• company logo and name, black or white back ground

```html
<!DOCTYPE html>
<html lang="en">
<head>
<meta charset="utf-8">
<title>Walsh &amp; Brand Pty Ltd – Business Card</title>
<link rel="stylesheet" href="https://fonts.googleapis.com/css2?family=Open+Sans:wght@400;600&display=swap">
<style>
  :root {
    --black: #000000;
    --paper: #fbfbfb;
    --ink: #333333;
    --grey: #959595;
    --frost-top: #eceded;
    --frost-bottom: #dcdcdd;
    --band-dark: #1c1c1c;
    --band-mid: #3a3a3a;
    --silver: #c9c9cb;
    --name-tone: #e6e1d6;
    --role-tone: #cdb98a;
    --stage: #cfcdca;
  }
  * { box-sizing: border-box; margin: 0; padding: 0; }
  html, body {
    width: 1200px;
    height: 969px;
    overflow: hidden;
    background: var(--stage);
    font-family: "Open Sans", Arial, sans-serif;
  }
  .card {
    position: absolute;
    left: 100px;
    top: 204px;
    width: 1000px;
    height: 562px;
    background: linear-gradient(170deg, var(--frost-top), var(--frost-bottom));
    border: 1px solid var(--paper);
    box-shadow: 0 12px 40px rgba(0,0,0,0.18);
    overflow: hidden;
  }
  .card__roof { position: absolute; inset: 0; width: 1000px; height: 562px; }
  .card__names {
    position: absolute;
    right: 44px;
    top: 34px;
    text-align: right;
    color: var(--name-tone);
  }
  .card__agents { font-size: 29px; font-weight: 400; letter-spacing: 0.2px; }
  .card__role { font-size: 20px; font-weight: 600; color: var(--role-tone); margin-top: 6px; }
  .brand {
    position: absolute;
    left: 60px;
    top: 372px;
    width: 400px;
    display: flex;
    align-items: center;
    justify-content: center;
    gap: 14px;
  }
  .brand__square { width: 22px; height: 22px; background: var(--ink); }
  .brand__name {
    font-size: 21px;
    font-weight: 600;
    letter-spacing: 1.5px;
    color: var(--ink);
    text-transform: uppercase;
  }
  .card__divider {
    position: absolute;
    left: 490px;
    top: 250px;
    width: 2px;
    height: 250px;
    background: var(--grey);
    opacity: 0.7;
  }
  .contact {
    position: absolute;
    left: 549px;
    top: 250px;
    color: var(--ink);
    font-size: 22px;
    line-height: 1.35;
  }
  .contact__address { margin-bottom: 22px; }
  .contact__list { list-style: none; }
  .contact__item { display: flex; align-items: center; gap: 16px; height: 37px; }
  .contact__icon { width: 22px; height: 22px; fill: var(--ink); flex: none; }
</style>
</head>
<body>
  <div class="card">
    <svg class="card__roof" viewBox="0 0 1000 562" aria-hidden="true">
      <defs>
        <linearGradient id="bandShade" x1="0" y1="0" x2="1" y2="0">
          <stop offset="0" stop-color="var(--band-mid)"/>
          <stop offset="0.5" stop-color="var(--band-dark)"/>
          <stop offset="1" stop-color="var(--band-mid)"/>
        </linearGradient>
      </defs>
      <polygon points="0,0 1000,0 1000,265 207,13 0,148" fill="url(#bandShade)"/>
      <polyline points="0,150 207,16 1000,268" fill="none" stroke="var(--silver)" stroke-width="7"/>
    </svg>

    <div class="card__names">
      <p class="card__agents">Owen Walsh &amp; Lucy Brand</p>
      <p class="card__role">Sales Agents &amp; Onsite Manager</p>
    </div>

    <div class="brand">
      <span class="brand__square"></span>
      <span class="brand__name">Walsh &amp; Brand Pty Ltd.</span>
    </div>

    <div class="card__divider"></div>

    <div class="contact">
      <p class="contact__address">3/42 Marlow Crescent<br>FERNLEA QLD 4213</p>
      <ul class="contact__list">
        <li class="contact__item">
          <svg class="contact__icon" viewBox="0 0 24 24"><path d="M6.6 10.8a15.2 15.2 0 0 0 6.6 6.6l2.2-2.2a1 1 0 0 1 1-.25 11.4 11.4 0 0 0 3.6.57 1 1 0 0 1 1 1V20a1 1 0 0 1-1 1A17 17 0 0 1 3 4a1 1 0 0 1 1-1h3.5a1 1 0 0 1 1 1c0 1.25.2 2.45.57 3.57a1 1 0 0 1-.25 1z"/></svg>
          <span>07 5948 2063</span>
        </li>
        <li class="contact__item">
          <svg class="contact__icon" viewBox="0 0 24 24"><path d="M7 1h10a2 2 0 0 1 2 2v18a2 2 0 0 1-2 2H7a2 2 0 0 1-2-2V3a2 2 0 0 1 2-2zm0 3v14h10V4zm5 15.5a1.2 1.2 0 1 0 0 2.4 1.2 1.2 0 0 0 0-2.4z"/></svg>
          <span>0431 857 219</span>
        </li>
        <li class="contact__item">
          <svg class="contact__icon" viewBox="0 0 24 24"><path d="M6 2h10l2 2v5H6zM3 10h18a2 2 0 0 1 2 2v7h-4v3H5v-3H1v-7a2 2 0 0 1 2-2zm4 7v3h10v-3z"/></svg>
          <span>07 5948 2174</span>
        </li>
        <li class="contact__item">
          <svg class="contact__icon" viewBox="0 0 24 24"><circle cx="12" cy="12" r="10"/><path d="M8 7c2 0 3 1 3 2.5S9 12 10 13.5 9 17 8 18M14 5c1 2 3 2 4 3M13 14c1.5 0 3 1 3 3" stroke="var(--frost-top)" stroke-width="1.6" fill="none"/></svg>
          <span>www.walshbrand.com</span>
        </li>
      </ul>
    </div>
  </div>
</body>
</html>
```